Stationery Design Project

I need a stationary design for our company. we are based in Houston, TX and we are called Mira Vell Lending. And we are wanting to brand our MoneyMendPlus program, which includes our tax preparation and restoration, credit repair service. Although our business offers other programs, we are interested in mainly focusing on The MoneyMendPlus program. We are looking for way to brand our ourselves and I believe that a great stationery design will help in achieving this goal. Our logo design is blue and light blue. the slogan is orange.

Industry/Entity Type

Business

Requirements
Must have
• Address: 30871 Calloway Ln. B-22
Houston, TX 75419
Tel. 555-318-6207
Fax 555-294-7153
www.miravelllending.example
info@miravelllending.example
Our Slogan: Confidence, Renewed!

```html
<!DOCTYPE html>
<html lang="en">
<head>
<meta charset="utf-8">
<title>Mira Vell Lending – Business Card</title>
<link href="https://fonts.googleapis.com/css2?family=Tinos:wght@400;700&display=swap" rel="stylesheet">
<style>
  :root {
    --backdrop: #ece8e2;
    --card: #ffffff;
    --card-edge: #3a3a3a;
    --navy: #163f66;
    --frame-blue: #c9def2;
    --brand-blue: #0f5f9c;
    --band-top: #0a8fca;
    --band-bottom: #0f3f6e;
    --orange: #f0922a;
    --rule-orange: #f2a23a;
    --white: #ffffff;
    --divider: rgba(255,255,255,0.55);
  }
  * { box-sizing: border-box; margin: 0; padding: 0; }
  html, body {
    width: 1200px; height: 1071px; overflow: hidden;
    background: var(--backdrop);
    font-family: "Tinos", "Times New Roman", serif;
  }
  .stage { position: relative; width: 1200px; height: 1071px; }

  .card {
    position: absolute; width: 815px; height: 465px;
    background: var(--card);
    border: 1px solid var(--card-edge);
    overflow: hidden;
  }
  .card--front { left: 45px; top: 48px; }
  .card--back { left: 326px; top: 550px; }

  /* front */
  .brand-name {
    position: absolute; left: 0; width: 815px; top: 155px;
    text-align: center; font-size: 66px; color: var(--brand-blue);
    font-weight: 400; letter-spacing: -0.5px;
  }
  .slogan {
    position: absolute; left: 0; width: 815px; top: 256px;
    text-align: center; font-size: 30px; font-weight: 700;
    color: var(--orange); letter-spacing: 3.5px;
  }
  .accent-rule {
    position: absolute; left: 0; top: 309px; width: 100%; height: 4px;
    background: var(--rule-orange);
  }
  .contact-band {
    position: absolute; left: 0; top: 317px; width: 100%; height: 148px;
    background: linear-gradient(to bottom, var(--band-top), var(--band-bottom));
    color: var(--white);
  }
  .address {
    position: absolute; right: 457px; top: 37px;
    text-align: right; font-size: 21px; line-height: 29px; font-style: normal;
  }
  .band-divider {
    position: absolute; left: 386px; top: 13px; width: 1px; height: 122px;
    background: var(--divider);
  }
  .contact-list {
    position: absolute; left: 413px; top: 8px; list-style: none;
    font-size: 21px; line-height: 31px;
  }
  .contact-list li { display: flex; align-items: center; gap: 9px; }
  .contact-list svg { width: 18px; height: 18px; flex: none; }

  /* back */
  .name-panel {
    position: absolute; left: 247px; top: 51px; width: 320px; height: 320px;
    background: var(--navy);
    border: 11px solid var(--frame-blue);
  }
  .back-name {
    position: absolute; left: 0; width: 100%; top: 227px;
    text-align: center; font-size: 27px; color: var(--white);
  }
  .back-url {
    position: absolute; left: 0; width: 815px; top: 411px;
    text-align: center; font-size: 22px; color: var(--navy);
    letter-spacing: 4px;
  }
  .back-url strong { font-weight: 700; }
</style>
</head>
<body>
<main class="stage">
  <section class="card card--front" aria-label="Card front">
    <div class="brand-name">MoneyMendPlus</div>
    <div class="slogan">Confidence, Renewed!</div>
    <div class="accent-rule"></div>
    <div class="contact-band">
      <address class="address">
        30871 Calloway Ln. B-22<br>Houston, TX 75419
      </address>
      <div class="band-divider"></div>
      <ul class="contact-list">
        <li>
          <svg viewBox="0 0 20 20" aria-hidden="true"><circle cx="10" cy="10" r="9" fill="none" stroke="#fff" stroke-width="1.5"/><path d="M7 5c-1 1-1 3 0 5s3 4 5 5c1 .3 2 0 2.5-.7l-1.8-1.8-1.4.8c-1-.5-2.2-1.7-2.7-2.7l.8-1.4L7.6 4.4z" fill="#fff"/></svg>
          555-318-6207
        </li>
        <li>
          <svg viewBox="0 0 20 20" aria-hidden="true"><rect x="5" y="3" width="10" height="5" fill="#fff"/><rect x="2" y="8" width="16" height="7" rx="1.5" fill="#fff"/><rect x="5" y="13" width="10" height="4" fill="#fff" stroke="#0c5f98" stroke-width="1"/></svg>
          555-294-7153
        </li>
        <li>
          <svg viewBox="0 0 20 20" aria-hidden="true"><path d="M2 8l8-5 8 5v9H2z" fill="#fff"/><path d="M2 8l8 5 8-5" fill="none" stroke="#0c5f98" stroke-width="1.3"/></svg>
          info@miravelllending.example
        </li>
        <li>
          <svg viewBox="0 0 20 20" aria-hidden="true"><g fill="none" stroke="#fff" stroke-width="1.3"><circle cx="10" cy="10" r="8"/><ellipse cx="10" cy="10" rx="3.5" ry="8"/><path d="M2 10h16M3.5 6h13M3.5 14h13"/></g></svg>
          www.miravelllending.example
        </li>
      </ul>
    </div>
  </section>

  <section class="card card--back" aria-label="Card back">
    <div class="name-panel">
      <div class="back-name">Mira Vell Lending</div>
    </div>
    <div class="back-url">www.<strong>miravelllending</strong>.example</div>
  </section>
</main>
</body>
</html>
```